Vision, Mission and Culture Posters

We have written text paragraphs for our company vision and mission and need them made into a2 or a3 sized posters using our logo for inspiration for colour. Our company culture has 10 paragraphs and we'd like this to be a single poster of a2 or a1. Each poster should have the logo on and share common design. It's not a complex job really.

Industry/Entity Type

It Company

Requirements
Nice to have
• These will be going up on our office wall so need to be clear to read from a distance and look professional but also not stodgy.

```html
<!DOCTYPE html>
<html lang="en">
<head>
<meta charset="utf-8">
<title>Company Values</title>
<link href="https://fonts.googleapis.com/css2?family=Alfa+Slab+One&family=Bebas+Neue&family=Caveat:wght@500&family=Lato:wght@400;900&display=swap" rel="stylesheet">
<style>
:root{
  --yellow:#fff200;
  --black:#111111;
  --red:#d62027;
  --num-red:#cf2a2f;
  --text:#1d1d1d;
  --paper-mid:#ffffff;
  --paper-edge:#e6e6e6;
}
*{margin:0;padding:0;box-sizing:border-box}
html,body{width:1200px;height:847px;overflow:hidden}
body{background:#fff;font-family:"Lato",Arial,sans-serif;color:var(--text)}
.poster{position:relative;width:1200px;height:847px;overflow:hidden;
  background:radial-gradient(ellipse at 55% 50%,var(--paper-mid) 35%,var(--paper-edge) 100%)}
.bands{position:absolute;inset:0;width:1200px;height:847px}
.brand{position:absolute;left:36px;top:30px;width:346px;height:100px;background:var(--yellow);
  border:4px solid var(--black);border-radius:10px;display:flex;align-items:center;gap:16px;padding-left:26px}
.brand-mark{width:34px;height:34px;background:var(--black);flex:none}
.brand-name{font-family:"Lato",Arial,sans-serif;font-weight:900;font-size:27px;line-height:1.05;color:var(--black)}
.title{position:absolute;left:408px;top:34px;width:630px;height:99px;background:var(--black);border-radius:12px;
  display:flex;align-items:center;justify-content:center;overflow:hidden}
.title h1{font-family:"Bebas Neue",Impact,sans-serif;font-weight:400;font-size:112px;line-height:1;color:var(--yellow);
  letter-spacing:1px;white-space:nowrap;margin-top:8px}
.value{position:absolute;width:554px}
.value.left{left:18px}
.value.right{left:628px}
.value h2{font-family:"Alfa Slab One",Georgia,serif;font-weight:400;font-size:33px;line-height:1;color:var(--yellow);
  -webkit-text-stroke:5px var(--black);paint-order:stroke fill;letter-spacing:0.5px;white-space:nowrap;
  text-shadow:2px 2px 0 var(--black)}
.value .num{position:absolute;left:2px;font-family:"Caveat",cursive;font-weight:500;font-size:30px;color:var(--num-red);line-height:1}
.value p{margin-left:43px;margin-top:8px;font-size:11px;line-height:14.8px;text-align:justify;width:511px}
</style>
</head>
<body>
<div class="poster">
  <svg class="bands" viewBox="0 0 1200 847" aria-hidden="true">
    <path d="M0 0 H1200 V34 L1088 138 Q1076 150 1056 150 H0 Z" fill="var(--yellow)" stroke="var(--black)" stroke-width="3"/>
    <path d="M0 818 L1140 806 Q1188 804 1202 822 V850 H0 Z" fill="var(--red)" stroke="var(--black)" stroke-width="3"/>
  </svg>

  <div class="brand">
    <span class="brand-mark"></span>
    <span class="brand-name">Kerbside<br>Bay Hire</span>
  </div>
  <div class="title"><h1>COMPANY VALUES</h1></div>

  <section class="value left" style="top:183px">
    <h2>COMMUNICATION</h2>
    <span class="num" style="top:68px">01</span>
    <p>We believe in open communication providing our customers, colleagues and others with honest, accurate, concise and prompt information relevant to their needs to ensure everyone always has a sound understanding of any matter being communicated. We are polite, friendly and warm and we use good communication as a means of enhancing our customer experience.</p>
  </section>

  <section class="value left" style="top:312px">
    <h2>EDUCATION</h2>
    <span class="num" style="top:70px">02</span>
    <p>We believe in the importance of continual learning and education and thrive on helping our colleagues by sharing our knowledge and learnings. We learn from our mistakes and use them to build a better, stronger, closer team environment. Understanding that everyone's needs are different and that we learn in different ways, we challenge our people to constantly improve their professional development in a way that works best for them.</p>
  </section>

  <section class="value left" style="top:452px">
    <h2>PROFESSIONALISM</h2>
    <span class="num" style="top:70px">03</span>
    <p>We represent ourselves as professionals and our business to the best of our abilities at all times taking particular care to give the best impression of ourselves to those we interact with during the course of our working days whether that be by phone, email or in person. We are always on time, well presented, well prepared and work hard to succeed.</p>
  </section>

  <section class="value left" style="top:580px">
    <h2>OWNERSHIP</h2>
    <span class="num" style="top:60px">04</span>
    <p>We are each fully responsible for our roles and for our contribution to the success of our business. We are accountable for our results, our ability to improve at what we do, our mistakes and what we do to correct them.</p>
  </section>

  <section class="value left" style="top:690px">
    <h2>COMMERCIAL AWARENESS</h2>
    <span class="num" style="top:70px">05</span>
    <p>We understand that in a small business everything we do can impact the success of our business and we commit ourselves to thinking about the impact on our business of all the decisions we make before we make them. We consider cost against benefit, remembering the cheapest option doesn't always give the greatest benefit, the best value use of our time, who benefits from what we do and how it benefits our business.</p>
  </section>

  <section class="value right" style="top:173px">
    <h2>BALANCE</h2>
    <span class="num" style="top:64px">06</span>
    <p>We try to find the best balance in our lives between our responsibilities, obligations, duties and desires whilst still ensuring we have time to devote to friends, families, fun and life. We try to balance our opinions and thoughts with those of others and believe that with balance comes fairness, integrity, self-control and a great attitude.</p>
  </section>

  <section class="value right" style="top:300px">
    <h2>CUSTOMER SERVICE</h2>
    <span class="num" style="top:68px">07</span>
    <p>We believe that without our customers we would not be successful and understand the outstanding level of service we give them is critical to our continued success, even down to the smallest action whenever that may be required from us. We go out of our way to help any customer with an issue and are only satisfied when we have helped them achieve a fair outcome they are happy with.</p>
  </section>

  <section class="value right" style="top:429px">
    <h2>CONSISTENCY</h2>
    <span class="num" style="top:62px">08</span>
    <p>We believe in consistency of our work, our approach, our positive attitude and our actions to set a standard at which our colleagues and customers feel a level of familiarity that strengthens our relationship whilst representing ourselves and our business to their best.</p>
  </section>

  <section class="value right" style="top:542px">
    <h2>SUCCESS</h2>
    <span class="num" style="top:62px">09</span>
    <p>We understand success isn't given, it is earned every day, piece by piece. We are driven to succeed as an individual and as a team and we support each other in earning that success. We are not afraid to celebrate our successes to acknowledge our hard work and dedication to our achieving our goals.</p>
  </section>

  <section class="value right" style="top:655px">
    <h2>COMMITMENT</h2>
    <span class="num" style="top:80px">10</span>
    <p>We are committed to the company vision, to the mission and to upholding the company culture as well as showing the company the same commitment it has shown to us. We talk about our vision, mission and culture often, use them to help guide ourselves and our colleagues as we go about our work. We are not afraid to let our colleagues know when we feel they are not showing the right commitment to our vision, mission and culture but make sure we do so in a positive and helpful way to ensure they can get back on track as easily as possible.</p>
  </section>
</div>
</body>
</html>
```